Custom Manufacturing Company square space website design

I own a custom manufacturing company that uses precision cutting technology to manufacture project components over a couple industries. We have an industrial CNC router and state of the art edge bander and cut a lot of cabinetry components for cabinet shops, builders, closet companies, ect. We offer design and assembly for any cabinetry or can build cabinets to spec. We also cut components for other industries out of wood, plastics, acryclics, ect. We offer design engineering services, product development protype services. we have a 3D printer farm. We want our communicate trust, dependability, and the value we place on client relationships.

We essentially want a credibility website. Landing page and drops downs for services we offer, capabilites, about us, contact

```html
<!DOCTYPE html>
<html lang="en">
<head>
<meta charset="utf-8">
<title>Northfield CNC</title>
<link href="https://fonts.googleapis.com/css2?family=Krona+One&family=Inter:wght@400;500;600&display=swap" rel="stylesheet">
<style>
:root{
  --ink:#111111;
  --dark:#1f1f1f;
  --dark-2:#2a2a2a;
  --white:#ffffff;
  --text:#333333;
  --muted:#8a8a8a;
  --line:#e6e6e6;
  --field:#ffffff;
  --photo-wood:#7a6a58;
  --photo-navy:#3c4668;
}
*{box-sizing:border-box;margin:0;padding:0}
html,body{width:1200px;height:4119px;overflow:hidden}
body{position:relative;background:var(--white);font-family:"Inter",sans-serif;color:var(--text)}
.abs{position:absolute}
.display{font-family:"Krona One",sans-serif;color:var(--ink);letter-spacing:1px}
.btn{position:absolute;display:flex;align-items:center;justify-content:center;font-family:"Krona One",sans-serif;font-size:13px;border-radius:3px}
.btn-dark{background:var(--ink);color:var(--white);box-shadow:0 6px 14px rgba(0,0,0,.25)}
.btn-light{background:var(--white);color:var(--ink)}
.rule{position:absolute;height:2px;background:linear-gradient(90deg,transparent,var(--ink) 20%,var(--ink) 80%,transparent)}
.rule-light{background:linear-gradient(90deg,var(--white),var(--white) 70%,transparent)}

/* header */
.topbar{left:330px;top:0;width:870px;height:46px;background:var(--ink);clip-path:polygon(0 0,100% 0,100% 100%,44px 100%)}
.topbar-item{top:12px;display:flex;align-items:center;gap:12px;color:var(--white);font-size:15px}
.icon-circle{width:30px;height:30px;border-radius:50%;background:var(--white);display:flex;align-items:center;justify-content:center}
.social{width:30px;height:30px;border-radius:50%;background:var(--white);top:8px}
.brand{left:98px;top:6px;width:160px;text-align:center}
.brand-mark{width:66px;height:48px;border:2px solid var(--ink);margin:0 auto 6px}
.brand-name{font-family:"Krona One",sans-serif;font-size:17px;color:var(--ink);letter-spacing:2px}
.nav{top:68px;left:437px;display:flex;gap:42px;font-family:"Krona One",sans-serif;font-size:14px;color:var(--ink)}

/* hero */
.hero-frame{left:0;top:102px;width:1200px;height:598px;background:var(--ink);clip-path:polygon(0 0,100% 0,100% 87%,91% 100%,9% 100%,0 87%)}
.hero-photo{left:0;top:102px;width:1200px;height:582px;background:linear-gradient(180deg,#8d9a7a 0%,#8a7c68 35%,var(--photo-wood) 55%,var(--photo-navy) 100%);clip-path:polygon(0 0,100% 0,100% 85%,91% 100%,9% 100%,0 85%)}
.hero-panel{left:350px;top:236px;width:560px;height:314px;background:rgba(40,40,40,.7);border-radius:14px}
.hero-title{left:0;width:1200px;top:268px;text-align:center;font-family:"Krona One",sans-serif;font-size:47px;line-height:57px;color:var(--white);letter-spacing:2px}
.hero-text{left:350px;width:500px;margin-left:30px;top:385px;text-align:center;color:var(--white);font-size:15px;line-height:31px}
.scroll-down{left:580px;top:677px;width:40px;height:40px;border-radius:50%;background:var(--white);box-shadow:0 3px 8px rgba(0,0,0,.25);display:flex;align-items:center;justify-content:center}

/* components */
.section-title{left:0;width:1200px;text-align:center;font-size:26px}
.intro{left:150px;width:900px;text-align:center;font-size:15px;line-height:31px;color:var(--text)}
.component{width:107px;top:928px;text-align:center}
.component-box{width:107px;height:99px;border:3px solid #9a9a9a;border-radius:4px;display:flex;align-items:center;justify-content:center;background:var(--white)}
.component-label{margin-top:20px;font-size:16px;color:var(--ink);white-space:nowrap;margin-left:-40px;width:187px}

/* about */
.about{left:0;top:1225px;width:1200px;height:550px;background:linear-gradient(90deg,#222 0%,#2b2b2b 60%,#262626 100%)}
.about-ring{left:105px;top:1283px;width:434px;height:434px;border-radius:50%;border:4px solid var(--white)}
.about-photo{left:118px;top:1296px;width:408px;height:408px;border-radius:50%;background:radial-gradient(circle at 45% 45%,#c9a77a 0%,#8b6c4a 40%,#3b3b3b 80%)}
.about-title{left:620px;top:1292px;font-size:26px;color:var(--white)}
.about-text{left:620px;top:1355px;width:490px;color:#e8e8e8;font-size:15px;line-height:31px}

/* services */
.card{top:1932px;width:318px;background:var(--white);border-radius:8px;box-shadow:0 4px 14px rgba(0,0,0,.12);overflow:hidden;text-align:center}
.card-img{height:246px}
.card-name{font-family:"Krona One",sans-serif;font-size:15px;line-height:31px;color:var(--ink)}
.card-feature{background:var(--ink);padding:0 14px 14px;border-radius:10px;top:1932px;width:318px}
.card-feature .inner{background:var(--white);border-radius:0 0 10px 10px;text-align:center;padding:14px 18px 16px}
.arrow{width:24px;height:24px;border-radius:50%;border:1.5px solid #666;display:flex;align-items:center;justify-content:center;top:2061px}

/* capabilities */
.capabilities{left:0;top:2520px;width:1200px;height:652px;background:linear-gradient(90deg,#232323,#2c2c2c 55%,#242424)}
.cap-item{left:98px;width:470px;display:flex;gap:15px;color:#e8e8e8;font-size:15px;line-height:31px}
.cap-item svg{flex:none;margin-top:6px}
.cap-photo{left:643px;top:2620px;width:457px;height:440px;border-radius:40px 40px 0 0;background:linear-gradient(135deg,#8b7a62 0%,#6a5a48 30%,#4b5560 65%,#2f2f2f 100%)}
.cap-outline{left:885px;top:2606px;width:230px;height:220px;border:3px solid var(--white);border-left:none;border-bottom:none;border-radius:0 50px 0 0}
.cap-outline-side{left:1112px;top:2650px;width:3px;height:140px;background:var(--white);border-radius:0 0 20px 0}

/* contact */
.field{background:var(--field);border-radius:4px;box-shadow:0 2px 10px rgba(0,0,0,.12);font-size:13px;color:var(--muted);padding:16px 17px}

/* footer */
.footer{left:0;top:3706px;width:1200px;height:413px;background:#1d1d1d}
.foot-head{font-family:"Krona One",sans-serif;font-size:18px;color:var(--white)}
.foot-list{list-style:none;color:var(--white);font-size:15px}
.foot-list li{display:flex;align-items:center;gap:12px;height:31px}
.foot-contact{display:flex;align-items:center;gap:14px;color:var(--white);font-size:15px}
.foot-icon{width:38px;height:38px;border-radius:50%;background:var(--white);display:flex;align-items:center;justify-content:center;flex:none}
.foot-social{width:32px;height:32px;border-radius:50%;background:var(--white);top:3934px}
</style>
</head>
<body>

<!-- Header -->
<div class="abs topbar"></div>
<div class="abs topbar-item" style="left:451px">
  <span class="icon-circle"><svg width="15" height="15" viewBox="0 0 24 24"><path d="M6.6 10.8a15 15 0 006.6 6.6l2.2-2.2a1 1 0 011-.25 11.4 11.4 0 003.6.6 1 1 0 011 1V20a1 1 0 01-1 1A17 17 0 013 4a1 1 0 011-1h3.5a1 1 0 011 1c0 1.25.2 2.45.6 3.6a1 1 0 01-.25 1z" fill="#111"/></svg></span>
  +1 555 010 2040
</div>
<div class="abs topbar-item" style="left:680px">
  <span class="icon-circle"><svg width="15" height="15" viewBox="0 0 24 24"><rect x="3" y="5" width="18" height="14" rx="2" fill="#111"/><path d="M3 7l9 6 9-6" stroke="#fff" stroke-width="1.6" fill="none"/></svg></span>
  info@northfieldcnc.com
</div>
<div class="abs social" style="left:944px"></div>
<div class="abs social" style="left:987px"></div>
<div class="abs social" style="left:1030px"></div>
<div class="abs social" style="left:1073px"></div>

<div class="abs brand">
  <div class="brand-mark"></div>
  <div class="brand-name">NORTHFIELD</div>
</div>
<nav class="abs nav"><span>Home</span><span>Services we offer</span><span>Capabilities</span><span>About Us</span><span>Contact Us</span></nav>

<!-- Hero -->
<div class="abs hero-frame"></div>
<div class="abs hero-photo" role="img" aria-label="Kitchen under construction with navy cabinets and countertop templates"></div>
<div class="abs hero-panel"></div>
<h1 class="abs hero-title">WELCOME TO<br>NORTHFIELD CNC</h1>
<p class="abs hero-text">Lorem ipsum dolor sit amet, consectetur adipiscing elit, sed do eiusmod tempor incididunt ut labore et dolore magna aliqua.</p>
<div class="btn btn-light" style="left:533px;top:457px;width:134px;height:46px;">Get Started</div>
<div class="abs scroll-down"><svg width="14" height="14" viewBox="0 0 24 24"><path d="M5 9l7 7 7-7" stroke="#111" stroke-width="3" fill="none"/></svg></div>

<!-- Cabinetry components -->
<h2 class="abs display section-title" style="top:768px">CABINETRY COMPONENTS</h2>
<div class="rule" style="left:505px;top:819px;width:190px"></div>
<p class="abs intro" style="top:836px">Lorem ipsum dolor sit amet, consectetur adipiscing elit, sed do eiusmod tempor incididunt ut labore et dolore magna aliqua. Ut enim ad minim veniam, quis nostrud exercitation ullamco laboris nisi ut aliquip ex ea commodo consequat.</p>

<div class="abs component" style="left:241px">
  <div class="component-box"><svg width="60" height="52" viewBox="0 0 60 52" fill="none" stroke="#111" stroke-width="2"><rect x="2" y="2" width="56" height="48"/><rect x="10" y="14" width="18" height="26"/><line x1="34" y1="16" x2="50" y2="16"/><line x1="34" y1="24" x2="50" y2="24"/><line x1="34" y1="32" x2="50" y2="32"/><line x1="2" y1="8" x2="58" y2="8"/></svg></div>
  <div class="component-label">Cabinet Shops</div>
</div>
<div class="abs component" style="left:444px">
  <div class="component-box"><svg width="60" height="56" viewBox="0 0 60 56" fill="none" stroke="#111" stroke-width="2"><path d="M14 22a16 16 0 0132 0z"/><line x1="10" y1="22" x2="50" y2="22"/><path d="M6 54v-10a12 12 0 0112-12h24a12 12 0 0112 12v10"/><rect x="34" y="36" width="14" height="16"/></svg></div>
  <div class="component-label">Builders</div>
</div>
<div class="abs component" style="left:647px">
  <div class="component-box"><svg width="60" height="56" viewBox="0 0 60 56" fill="none" stroke="#111" stroke-width="2"><rect x="20" y="4" width="20" height="48"/><rect x="6" y="24" width="14" height="28"/><rect x="40" y="18" width="14" height="34"/><line x1="2" y1="52" x2="58" y2="52"/><line x1="25" y1="12" x2="35" y2="12"/><line x1="25" y1="20" x2="35" y2="20"/><line x1="25" y1="28" x2="35" y2="28"/></svg></div>
  <div class="component-label">Closet Companies</div>
</div>
<div class="abs component" style="left:850px">
  <div class="component-box"><svg width="60" height="56" viewBox="0 0 60 56" fill="none" stroke="#111" stroke-width="2"><rect x="8" y="4" width="44" height="12"/><rect x="8" y="22" width="44" height="28"/><line x1="30" y1="22" x2="30" y2="50"/><line x1="8" y1="36" x2="52" y2="36"/><line x1="4" y1="19" x2="56" y2="19"/></svg></div>
  <div class="component-label">Cabinet Shops</div>
</div>
<div class="btn btn-dark" style="left:533px;top:1105px;width:134px;height:47px;">View More</div>

<!-- About -->
<div class="abs about"></div>
<div class="abs about-ring"></div>
<div class="abs about-photo" role="img" aria-label="Craftsman assembling a wooden chair frame with a power drill"></div>
<h2 class="abs display about-title" style="color:var(--white)">ABOUT US</h2>
<div class="rule rule-light" style="left:620px;top:1336px;width:192px"></div>
<p class="abs about-text">Sed ut perspiciatis unde omnis iste natus error sit voluptatem accusantium doloremque laudantium, totam rem aperiam, eaque ipsa quae ab illo inventore veritatis et quasi architecto beatae vitae dicta sunt explicabo. Nemo enim ipsam voluptatem quia voluptas sit aspernatur aut odit aut fugit, sed quia consequuntur magni dolores eos qui ratione voluptatem sequi nesciunt. Neque porro quisquam est, qui dolorem ipsum quia dolor sit amet, consectetur, adipisci velit, sed quia non numquam eius modi tempora incidunt ut labore et dolore magnam aliquam quaerat voluptatem.</p>
<div class="btn btn-light" style="left:620px;top:1656px;width:132px;height:47px;">Read More</div>

<!-- Services -->
<h2 class="abs display section-title" style="top:1845px">SERVICES WE OFFER</h2>
<div class="rule" style="left:502px;top:1895px;width:196px"></div>

<div class="abs arrow" style="left:48px"><svg width="10" height="10" viewBox="0 0 24 24"><path d="M15 5l-7 7 7 7" stroke="#444" stroke-width="3" fill="none"/></svg></div>
<div class="abs arrow" style="left:1128px"><svg width="10" height="10" viewBox="0 0 24 24"><path d="M9 5l7 7-7 7" stroke="#444" stroke-width="3" fill="none"/></svg></div>

<div class="abs card" style="left:98px;height:330px;border-bottom:6px solid #9a9a9a">
  <div class="card-img" role="img" aria-label="Worker fitting shelving in a built-in closet" style="background:linear-gradient(135deg,#d9c7a8,#b98a4e 55%,#7a5c3c)"></div>
  <div class="card-name" style="padding-top:14px">Design Engineering<br>Services</div>
</div>

<div class="abs card-feature" style="left:441px;height:490px">
  <div role="img" aria-label="3D printer producing a prototype part" style="height:246px;margin:0 -14px;border-radius:10px 10px 0 0;background:linear-gradient(135deg,#2d3a4a,#55606c 50%,#c2692e)"></div>
  <div class="inner">
    <div class="card-name">Product Development<br>Prototype Services</div>
    <p style="font-size:14px;line-height:31px;margin-top:3px">Lorem ipsum dolor sit amet, consectetur adipiscing elit, labore et dolore magna aliqua.</p>
    <div style="font-family:'Krona One',sans-serif;font-size:15px;color:var(--ink);display:inline-block;border-bottom:2px solid var(--ink);line-height:26px;margin-top:2px">Read More</div>
  </div>
</div>

<div class="abs card" style="left:784px;height:330px;border-bottom:6px solid #9a9a9a">
  <div class="card-img" role="img" aria-label="Rows of 3D printers in a print farm" style="background:linear-gradient(180deg,#5a5a5a,#8a8a8a 45%,#c9573a 75%,#3a3a3a)"></div>
  <div class="card-name" style="padding-top:28px">3D Printer Farm</div>
</div>

<!-- Capabilities -->
<div class="abs capabilities"></div>
<h2 class="abs display" style="left:98px;top:2610px;font-size:26px;color:var(--white)">OUR CAPABILITIES</h2>
<div class="rule rule-light" style="left:98px;top:2658px;width:192px"></div>

<div class="abs cap-item" style="top:2687px"><svg width="30" height="30" viewBox="0 0 30 30" fill="none" stroke="#fff" stroke-width="1.6"><rect x="2" y="3" width="11" height="8"/><rect x="17" y="3" width="11" height="8"/><rect x="2" y="17" width="26" height="10"/><line x1="10" y1="17" x2="10" y2="27"/><line x1="19" y1="17" x2="19" y2="27"/></svg><span>Lorem ipsum dolor sit amet, consectetur adipiscing elit, sed do eiusmod tempor incididunt ut labore et dolore aliqua.</span></div>
<div class="abs cap-item" style="top:2771px"><svg width="30" height="30" viewBox="0 0 30 30" fill="none" stroke="#fff" stroke-width="1.6"><rect x="3" y="2" width="24" height="26"/><line x1="15" y1="2" x2="15" y2="28"/><rect x="7" y="8" width="4" height="12"/><rect x="19" y="8" width="4" height="12"/></svg><span>Lorem ipsum dolor sit amet, consectetur adipiscing elit, sed labore et dolore magna aliqua.</span></div>
<div class="abs cap-item" style="top:2855px"><svg width="30" height="30" viewBox="0 0 30 30" fill="none" stroke="#fff" stroke-width="1.6"><rect x="2" y="4" width="8" height="7"/><rect x="11" y="4" width="8" height="7"/><rect x="20" y="4" width="8" height="7"/><rect x="2" y="17" width="26" height="10"/><line x1="2" y1="22" x2="28" y2="22"/></svg><span>Lorem ipsum dolor sit amet, do eiusmod tempor incididunt ut labore et dolore aliqua.</span></div>
<div class="abs cap-item" style="top:2939px"><svg width="30" height="30" viewBox="0 0 30 30" fill="none" stroke="#fff" stroke-width="1.6"><rect x="5" y="2" width="20" height="26"/><line x1="5" y1="10" x2="25" y2="10"/><line x1="5" y1="19" x2="25" y2="19"/><line x1="13" y1="6" x2="17" y2="6"/><line x1="13" y1="14" x2="17" y2="14"/><line x1="13" y1="23" x2="17" y2="23"/></svg><span>Lorem ipsum dolor sit amet, consectetur do eiusmod tempor incididunt ut labore et dolore aliqua.</span></div>
<div class="btn btn-light" style="left:98px;top:3028px;width:132px;height:46px;">Read More</div>

<div class="abs cap-outline"></div>
<div class="abs cap-outline-side"></div>
<div class="abs cap-photo" role="img" aria-label="Technician assembling a white cabinet with a screwdriver"></div>
<svg class="abs" style="left:608px;top:2988px" width="108" height="100" viewBox="0 0 108 100">
  <g fill="#fff">
    <circle cx="4" cy="4" r="2"/><circle cx="20" cy="4" r="2"/>
    <circle cx="4" cy="20" r="2"/><circle cx="20" cy="20" r="2"/>
    <circle cx="4" cy="36" r="2"/><circle cx="20" cy="36" r="2"/>
    <circle cx="4" cy="52" r="2"/><circle cx="20" cy="52" r="2"/>
    <circle cx="4" cy="68" r="2"/><circle cx="20" cy="68" r="2"/><circle cx="36" cy="68" r="2"/><circle cx="52" cy="68" r="2"/><circle cx="68" cy="68" r="2"/><circle cx="84" cy="68" r="2"/><circle cx="100" cy="68" r="2"/>
    <circle cx="4" cy="84" r="2"/><circle cx="20" cy="84" r="2"/><circle cx="36" cy="84" r="2"/><circle cx="52" cy="84" r="2"/><circle cx="68" cy="84" r="2"/><circle cx="84" cy="84" r="2"/><circle cx="100" cy="84" r="2"/>
  </g>
</svg>

<!-- Contact -->
<h2 class="abs display section-title" style="top:3250px">CONTACT US</h2>
<div class="rule" style="left:486px;top:3300px;width:228px"></div>
<div class="abs field" style="left:181px;top:3345px;width:412px;height:48px">Name</div>
<div class="abs field" style="left:605px;top:3345px;width:412px;height:48px">Email</div>
<div class="abs field" style="left:181px;top:3408px;width:412px;height:48px">Phone Number</div>
<div class="abs field" style="left:605px;top:3408px;width:412px;height:48px">Subject</div>
<div class="abs field" style="left:181px;top:3470px;width:836px;height:86px">Message</div>
<div class="btn btn-dark" style="left:530px;top:3582px;width:138px;height:50px;font-family:'Inter',sans-serif;font-weight:600;font-size:15px">Submit</div>

<!-- Footer -->
<div class="abs footer"></div>
<div class="abs" style="left:168px;top:3780px;width:96px;height:70px;border:3px solid var(--white)"></div>
<div class="abs" style="left:100px;top:3870px;width:232px;text-align:center;font-family:'Krona One',sans-serif;font-size:24px;color:var(--white);letter-spacing:2px">NORTHFIELD</div>
<div class="abs foot-social" style="left:98px"></div>
<div class="abs foot-social" style="left:142px"></div>
<div class="abs foot-social" style="left:186px"></div>
<div class="abs foot-social" style="left:230px"></div>

<h3 class="abs foot-head" style="left:402px;top:3778px">Quick Links</h3>
<ul class="abs foot-list" style="left:402px;top:3810px">
  <li><svg width="14" height="12" viewBox="0 0 14 12"><path d="M0 6h11M7 1l5 5-5 5" stroke="#fff" stroke-width="2.2" fill="none"/></svg>Home</li>
  <li><svg width="14" height="12" viewBox="0 0 14 12"><path d="M0 6h11M7 1l5 5-5 5" stroke="#fff" stroke-width="2.2" fill="none"/></svg>Services we offer</li>
  <li><svg width="14" height="12" viewBox="0 0 14 12"><path d="M0 6h11M7 1l5 5-5 5" stroke="#fff" stroke-width="2.2" fill="none"/></svg>Capabilities</li>
  <li><svg width="14" height="12" viewBox="0 0 14 12"><path d="M0 6h11M7 1l5 5-5 5" stroke="#fff" stroke-width="2.2" fill="none"/></svg>About us</li>
  <li><svg width="14" height="12" viewBox="0 0 14 12"><path d="M0 6h11M7 1l5 5-5 5" stroke="#fff" stroke-width="2.2" fill="none"/></svg>Contact</li>
</ul>

<h3 class="abs foot-head" style="left:625px;top:3778px">Other Links</h3>
<ul class="abs foot-list" style="left:625px;top:3810px;font-size:14px">
  <li><svg width="14" height="12" viewBox="0 0 14 12"><path d="M0 6h11M7 1l5 5-5 5" stroke="#fff" stroke-width="2.2" fill="none"/></svg>FAQ</li>
  <li><svg width="14" height="12" viewBox="0 0 14 12"><path d="M0 6h11M7 1l5 5-5 5" stroke="#fff" stroke-width="2.2" fill="none"/></svg>Tems of Use</li>
  <li><svg width="14" height="12" viewBox="0 0 14 12"><path d="M0 6h11M7 1l5 5-5 5" stroke="#fff" stroke-width="2.2" fill="none"/></svg>Privacy Policy</li>
  <li><svg width="14" height="12" viewBox="0 0 14 12"><path d="M0 6h11M7 1l5 5-5 5" stroke="#fff" stroke-width="2.2" fill="none"/></svg>Support Links</li>
  <li><svg width="14" height="12" viewBox="0 0 14 12"><path d="M0 6h11M7 1l5 5-5 5" stroke="#fff" stroke-width="2.2" fill="none"/></svg>Conditions</li>
</ul>

<h3 class="abs foot-head" style="left:847px;top:3778px">Contact Us</h3>
<div class="abs foot-contact" style="left:847px;top:3821px;font-size:14px">
  <span class="foot-icon"><svg width="14" height="16" viewBox="0 0 24 28"><path d="M12 0a10 10 0 00-10 10c0 7 10 18 10 18s10-11 10-18A10 10 0 0012 0z" fill="#111"/><circle cx="12" cy="10" r="4" fill="#fff"/></svg></span>
  Northfield CNC, United States.
</div>
<div class="abs foot-contact" style="left:847px;top:3881px;font-size:14px">
  <span class="foot-icon"><svg width="15" height="15" viewBox="0 0 24 24"><rect x="3" y="5" width="18" height="14" rx="2" fill="#111"/><path d="M3 7l9 6 9-6" stroke="#fff" stroke-width="1.6" fill="none"/></svg></span>
  info@northfieldcnc.com
</div>
<div class="abs foot-contact" style="left:847px;top:3941px;font-size:14px">
  <span class="foot-icon"><svg width="15" height="15" viewBox="0 0 24 24"><path d="M6.6 10.8a15 15 0 006.6 6.6l2.2-2.2a1 1 0 011-.25 11.4 11.4 0 003.6.6 1 1 0 011 1V20a1 1 0 01-1 1A17 17 0 013 4a1 1 0 011-1h3.5a1 1 0 011 1c0 1.25.2 2.45.6 3.6a1 1 0 01-.25 1z" fill="#111"/></svg></span>
  +1 555 010 2040
</div>

<div class="abs" style="left:98px;top:4033px;width:1004px;height:1px;background:#555"></div>
<p class="abs" style="left:0;width:1200px;top:4066px;text-align:center;color:var(--white);font-size:14px">Copyrights@2023.Northfield CNC.All Rights Reserved</p>

</body>
</html>
```